Property development business card design

New build residential property developers. I want a professional look but customer friendly so not too corporate. I'm not sure what logo will look best so open to designs with either. Thank you

Also i don't want both names on one card its 2 names for 2 different cards but with the same design.

Industry/Entity Type

Residential

Contact Information for Business Card

KTR Developments Ltd,
58 Fennel Lane,
Ipswich,
Suffolk,
IP7 4WD

Property Research Manager
Morven Tadlock

Managing Director
Dilan Perriwick

```html
<!DOCTYPE html>
<html lang="en">
<head>
<meta charset="utf-8">
<title>KTR Developments – Business Card</title>
<link rel="stylesheet" href="https://fonts.googleapis.com/css2?family=Open+Sans:wght@400;600;700&display=swap">
<style>
  :root{
    --page-bg:#e6e6e6;
    --card-bg:#ffffff;
    --brand-grey:#8a8a8a;
    --name-navy:#3a3f94;
    --body-ink:#2f2f2f;
    --blue-light:#1d9ad9;
    --blue-deep:#2b47ad;
    --swoosh-light:#c8c8c8;
    --swoosh-dark:#6e6e6e;
    --logo-dot:#1e88d0;
    --on-blue:#ffffff;
  }
  html,body{margin:0;padding:0;width:1200px;height:900px;overflow:hidden;background:var(--page-bg);}
  body{display:flex;align-items:center;justify-content:center;font-family:"Open Sans",Arial,sans-serif;}
  .business-card{position:relative;width:840px;height:480px;background:var(--card-bg);box-shadow:0 6px 22px rgba(0,0,0,.18);overflow:hidden;}
  .card-shapes{position:absolute;inset:0;}
  .brand{position:absolute;left:44px;top:52px;display:flex;align-items:center;gap:18px;}
  .brand-mark{width:96px;height:96px;border-radius:50%;background:var(--logo-dot);}
  .brand-name{font-size:28px;font-weight:600;color:var(--brand-grey);letter-spacing:1px;white-space:nowrap;}
  .holder{position:absolute;left:52px;top:262px;}
  .holder-name{margin:0;font-size:30px;font-weight:400;letter-spacing:2px;color:var(--name-navy);text-transform:uppercase;}
  .holder-role{margin:2px 0 0;font-size:20px;color:var(--body-ink);letter-spacing:.5px;}
  .holder-address{margin:26px 0 0;font-style:normal;font-size:20px;line-height:1.3;color:var(--body-ink);letter-spacing:.5px;}
  .contact-list{position:absolute;right:34px;top:60px;margin:0;padding:0;list-style:none;color:var(--on-blue);font-size:15px;letter-spacing:.3px;text-align:right;}
  .contact-list li{display:flex;justify-content:flex-end;align-items:center;gap:10px;height:32px;white-space:nowrap;}
  .contact-icon{width:17px;height:17px;flex:none;}
</style>
</head>
<body>
  <article class="business-card">
    <svg class="card-shapes" viewBox="0 0 840 480" width="840" height="480" aria-hidden="true">
      <defs>
        <linearGradient id="blue-panel" x1="0" y1="0" x2="0.3" y2="1">
          <stop offset="0" stop-color="var(--blue-light)"/>
          <stop offset="1" stop-color="var(--blue-deep)"/>
        </linearGradient>
        <linearGradient id="grey-swoosh" x1="0" y1="0" x2="0.4" y2="1">
          <stop offset="0" stop-color="var(--swoosh-dark)"/>
          <stop offset="0.6" stop-color="var(--swoosh-light)"/>
          <stop offset="1" stop-color="var(--swoosh-dark)"/>
        </linearGradient>
      </defs>
      <path class="swoosh" d="M420,0 L520,0 C620,120 675,300 690,480 L676,480 C645,300 560,120 420,0 Z" fill="url(#grey-swoosh)"/>
      <path class="blue-panel" d="M520,0 L840,0 L840,480 L690,480 C675,300 620,120 520,0 Z" fill="url(#blue-panel)"/>
    </svg>

    <div class="brand">
      <span class="brand-mark" aria-hidden="true"></span>
      <span class="brand-name">KTR DEVELOPMENTS</span>
    </div>

    <div class="holder">
      <h1 class="holder-name">Dilan Perriwick</h1>
      <p class="holder-role">Managing Director</p>
      <address class="holder-address">58 Fennel Lane, Ipswich<br>Suffolk IP7 4WD</address>
    </div>

    <ul class="contact-list">
      <li>01473 555 0142
        <svg class="contact-icon" viewBox="0 0 24 24" aria-label="phone"><path d="M6 3l3 0 2 5-2 1.5a11 11 0 0 0 5.5 5.5L16 13l5 2v3a2 2 0 0 1-2 2A17 17 0 0 1 4 5a2 2 0 0 1 2-2z" fill="none" stroke="#fff" stroke-width="1.8" stroke-linejoin="round"/></svg>
      </li>
      <li>07700 555 0198
        <svg class="contact-icon" viewBox="0 0 24 24" aria-label="mobile"><rect x="7" y="2" width="10" height="20" rx="2" fill="none" stroke="#fff" stroke-width="1.8"/><line x1="10.5" y1="18.5" x2="13.5" y2="18.5" stroke="#fff" stroke-width="1.8"/></svg>
      </li>
      <li>01473 555 0143
        <svg class="contact-icon" viewBox="0 0 24 24" aria-label="fax"><rect x="4" y="8" width="16" height="13" rx="1" fill="#fff"/><rect x="7" y="3" width="10" height="6" fill="#fff"/><line x1="7" y1="14" x2="17" y2="14" stroke="#2b6cc4" stroke-width="1.5"/><line x1="7" y1="17" x2="17" y2="17" stroke="#2b6cc4" stroke-width="1.5"/></svg>
      </li>
      <li>dilan@ktrdev.co.uk
        <svg class="contact-icon" viewBox="0 0 24 24" aria-label="email"><rect x="2" y="5" width="20" height="14" rx="1" fill="#fff"/><path d="M2 6l10 7 10-7" fill="none" stroke="#2b6cc4" stroke-width="1.6"/></svg>
      </li>
      <li>www.ktrdev.co.uk
        <svg class="contact-icon" viewBox="0 0 24 24" aria-label="website"><circle cx="12" cy="12" r="9.5" fill="none" stroke="#fff" stroke-width="1.8"/><ellipse cx="12" cy="12" rx="4" ry="9.5" fill="none" stroke="#fff" stroke-width="1.5"/><line x1="2.5" y1="12" x2="21.5" y2="12" stroke="#fff" stroke-width="1.5"/></svg>
      </li>
    </ul>
  </article>
</body>
</html>
```